Business Card and Letterhead for Pimlu - modern real estate business

I need a double sided business card design for Pimlu. Please see business card brief here https://files.trelvonadocs.com/sheet/r/7QzTmWbaXLJnoPEd-kRyUgFhHsstbvCe2qfoMxDa_pz/view?mode=shared

Please feel free to design the business cards however you feel best. I am happy to give some creative freedoms and then provide feedback from there.

Please then also create a letterhead to match the business card design

Colors

Designer to choose colors to be used in the design.

Requirements
Must have
• Must be a modern, elegant business card which looks very professional

```html
<!DOCTYPE html>
<html lang="en">
<head>
<meta charset="utf-8">
<title>Pimlu — Business Card</title>
<link rel="stylesheet" href="https://fonts.googleapis.com/css2?family=Roboto:wght@400;500;700&display=swap">
<style>
  :root {
    --brand-red: #e30613;
    --charcoal: #2a2a2a;
    --band-line: #2b2b2b;
    --white: #ffffff;
    --page-bg: #ececec;
    --photo-border: #6f6f6f;
  }
  * { box-sizing: border-box; margin: 0; padding: 0; }
  html, body {
    width: 1125px; height: 1200px; overflow: hidden;
    background: var(--page-bg);
    font-family: "Roboto", Arial, sans-serif;
  }
  .canvas { position: relative; width: 1125px; height: 1200px; }

  .card {
    position: absolute; left: 150px; width: 826px; height: 471px;
    box-shadow: 0 4px 14px rgba(0,0,0,0.25);
    overflow: hidden;
  }
  .card--front { top: 90px; background: var(--white); }
  .card--back { top: 640px; background: var(--charcoal); }

  .wordmark {
    position: absolute; color: var(--brand-red);
    font-weight: 700; letter-spacing: 2px; line-height: 1;
  }
  .card--front .wordmark { left: 43px; top: 122px; font-size: 78px; }
  .card--back .wordmark {
    left: 0; right: 0; top: 170px; text-align: center; font-size: 124px; letter-spacing: 4px;
  }

  .agent-photo {
    position: absolute; left: 598px; top: 78px; width: 154px; height: 170px;
    border: 2px solid var(--photo-border); border-radius: 12px;
    background: linear-gradient(180deg, #b9c6c9 0%, #8c9a86 45%, #2d2f33 72%, #1e1f22 100%);
  }

  .contact-band { position: absolute; left: 0; top: 298px; width: 826px; height: 173px; }

  .contact-list {
    position: absolute; left: 43px; top: 332px;
    color: var(--white); font-size: 18px; line-height: 22.5px; list-style: none;
  }
  .contact-list li { display: flex; align-items: center; }
  .contact-list .with-icon { margin-left: 0; }
  .contact-list .address-gap { margin-bottom: 6px; }
  .icon { width: 14px; height: 14px; margin-right: 12px; fill: var(--white); flex: none; }

  .agent-id {
    position: absolute; right: 69px; top: 372px; text-align: right; color: var(--white);
  }
  .agent-name { font-size: 26px; font-weight: 700; line-height: 32px; }
  .agent-title { font-size: 18px; font-weight: 500; line-height: 24px; }
</style>
</head>
<body>
<main class="canvas">
  <section class="card card--front" aria-label="Business card front">
    <div class="wordmark">Pimlu</div>
    <div class="agent-photo" role="img" aria-label="Portrait photo of the agent"></div>

    <svg class="contact-band" viewBox="0 0 826 173" aria-hidden="true">
      <polygon points="0,12 826,12 826,173 0,173" fill="var(--brand-red)"/>
      <polyline points="0,4 640,4 676,36 712,4 826,4" fill="none" stroke="var(--band-line)" stroke-width="7"/>
      <polygon points="650,13 702,13 676,30" fill="var(--white)"/>
    </svg>

    <ul class="contact-list">
      <li>PO Box 7319</li>
      <li class="address-gap">Larkfield NSW 2690</li>
      <li>
        <svg class="icon" viewBox="0 0 24 24"><path d="M6.6 10.8a15.1 15.1 0 0 0 6.6 6.6l2.2-2.2a1 1 0 0 1 1-.25 11.4 11.4 0 0 0 3.6.57 1 1 0 0 1 1 1V20a1 1 0 0 1-1 1A17 17 0 0 1 3 4a1 1 0 0 1 1-1h3.5a1 1 0 0 1 1 1c0 1.25.2 2.45.57 3.57a1 1 0 0 1-.25 1z"/></svg>
        0491 570 338
      </li>
      <li>
        <svg class="icon" viewBox="0 0 24 24"><path d="M2 6h20v12H2z M2 6l10 7 10-7" fill="var(--white)"/><path d="M2 6.5l10 7 10-7" fill="none" stroke="var(--brand-red)" stroke-width="1.6"/></svg>
        dane@pimlu.com
      </li>
      <li>
        <svg class="icon" viewBox="0 0 24 24"><circle cx="12" cy="12" r="10"/><path d="M2 12h20M12 2c3 3 3 17 0 20M12 2c-3 3-3 17 0 20" fill="none" stroke="var(--brand-red)" stroke-width="1.5"/></svg>
        www.pimlu.com
      </li>
    </ul>

    <div class="agent-id">
      <div class="agent-name">Dane Corrow</div>
      <div class="agent-title">Licenced Real Estate Agent</div>
    </div>
  </section>

  <section class="card card--back" aria-label="Business card back">
    <div class="wordmark">Pimlu</div>
  </section>
</main>
</body>
</html>
```